KRV Packaging design for beauty industry

Looking for my first product packaging design, tailored to reflect KRV’s branding and product benefits, along with mockup suggestions to bring it to life.

---

Front of the Box Copy
**Header**:
KRV Zenith Max Upright Dryer

**Subheader**:
Effortless Styling. Professional Results.

**Features (Use Icons + Text)**:
- **Adjustable Height**: Perfect for all users and settings.
- **Ionic Technology**: Faster drying, frizz-free results.
- **360° Heat Distribution**: Even styling every time.
- **Lightweight & Portable**: Easy to move and assemble.

**Call to Action (CTA)**:
*“Elevate Your Look with KRV Professional-Grade Tools.”*

---

### **Side Panel Copy**
**About KRV**:
"At KRV, we believe beauty is power. Our tools are designed with precision, ensuring every style feels as beautiful as you are."

**Key Benefits**:
- 3 Heat Settings for customizable control.
- Quiet operation for a professional salon experience.
- Compact foldable design for storage and travel.

**Contact Info**:
KRV Beauty | **www.KRVhome.com**
Customer Care: care@KRVhome.com

---

### **Back Panel Copy**
**Product Specifications**:
- Voltage: 110V-240V
- Adjustable Height Range: X to Y inches
- Dryer Weight: X lbs

**What’s Included**:
- 1 Stand-Up Dryer
- Adjustable Stand
- User Manual

**Care Instructions**:
"Clean with a damp cloth after use. Store in a cool, dry place."

**Certifications**:
(Include icons for UL, CE, RoHS, and recycling).

**Barcode Area**: Leave space for the UPC code.

---

### **Mockup Suggestions**
1. **Front View**:
- Use a glossy royal purple background with a clean, central placement of the KRV logo in metallic gold.
- Include a product photo or 3D render in high resolution showing the dryer in action or as a standalone image.
- Highlight features using icons with gold or white text.

2. **Side View**:
- Use a lifestyle image (e.g., a stylist using the dryer in a salon).
- Incorporate a vertical gold stripe or gradient to add luxury while separating text sections.

3. **Back View**:
- A clean layout with product details, specifications, and what's included.
- Use gold accents to frame sections for easy readability.

4. **Top Panel**:
- Simple branding with just the KRV logo and tagline: *"Kind, Radiant, Vivid."*

The competition:
https://www.brellomart.com/products/warm-glow-07314?ref=QzT81mPvLx4Wd0YhRk2NcBs7JuEa9FgVo3iXqH6yTn5KwLd

Feel free to use the phots by the "the completion" but remove logo and add KRV logo .
https://files.plovia.net/share/9Qw3LzRt7XvN2mKb5HcYp8DfJe4SaGu?mode=view_link
Size: 48x36.5x48 CM

Logo: https://files.plovia.net/share/9Qw3LzRt7XvN2mKb5HcYp8DfJe4SaGu?mode=view_link
Also im not able to attached the AI file of the logo. Please message me your email and I'll email it to you.

Thank you!
Happy designing!

Target Market(s)

Target Audience for KRV’s First Product Demographics: Age: 18-40 years old Gender: Primarily women Income Level: Middle to upper-middle income, willing to invest in quality beauty products. Geographics: Urban and suburban areas across the U.S., where beauty culture is strong and highly influenced by social media and fashion trends. Psychographics: Beauty Enthusiasts: Individuals who prioritize their appearance and enjoy experimenting with beauty products. Trendsetters: Consumers who follow the latest beauty trends, influenced by social media and influencers. Self-Expression Advocates: Those who see beauty as a form of self-care and a way to express their personality and confidence. Behavioral Characteristics: Purchase Habits: Frequently buy beauty tools and products online or in beauty supply stores. Look for high-quality, professional-grade, and aesthetically pleasing products. Product Expectations: Easy-to-use, reliable, and results-driven. Luxurious feel without an excessively high price point. Engagement: Active on social media platforms like Instagram, TikTok, and YouTube. Trust peer reviews, influencer recommendations, and user-generated content. Customer Needs: Products that simplify beauty routines. Tools and supplies that are versatile and cater to diverse beauty needs, particularly for African American women (a key segment for KRV).

Industry/Entity Type

Industry Overview Primary Industry: Beauty and Personal Care: Encompasses products and tools for hair, skin, nails, and cosmetics. Sub-Sector: Hair Care & Styling Tools: Includes professional-grade tools like dryers, flat irons, and curling wands, along with supporting products like shampoos, conditioners, and styling creams.

Font styles to use
Serif

Requirements
Must have
• Must-Haves for the Packaging Brand Identity: Prominent display of the KRV logo in metallic gold to reinforce brand recognition. Consistent use of royal purple as the background color with metallic gold and white typography for a luxurious feel. Clear Product Information: Product Name: Clearly labeled as "KRV Zenith Max Upright Dryer" on the front. Key Features: Use icons with text to highlight: Adjustable Height Ionic Technology 360° Heat Distribution Lightweight & Portable Visual Appeal: High-quality product image or 3D render showcasing the dryer. Lifestyle imagery on the side panels to show the product in use, emphasizing its professional and stylish appeal. Call to Action (CTA): Include a tagline like: “Elevate Your Look with KRV Professional-Grade Tools.” Functional Details: Product Specifications: Include voltage, dimensions, and weight on the back panel. What’s Included: Clearly list all box contents. Certifications and Compliance: Add icons for UL, CE, RoHS, and recycling to ensure credibility and eco-conscious appeal. Contact Information: Website: www.KRVhome.com Customer care email: care@KRVhome.com Barcode Area: Leave space for the UPC code on the back panel. Packaging Consistency: Uniform design elements across all panels for a cohesive look (color scheme, typography, and layout). Professional and Luxurious Finish: A glossy or matte finish with possible embossing on the logo for a premium touch.
Nice to have
• Nice-to-Have Elements Interactive Design Features: QR Code: Link to a demo video, tutorial, or assembly instructions for added customer engagement. Augmented Reality (AR): An AR feature that allows customers to see the dryer in a 360° view or visualize it in their space. Texture and Finishes: Embossed or Debossed Details: Highlight the KRV logo or key features with embossed or debossed effects for a tactile, premium feel. Spot UV Coating: Add gloss to key areas like the logo or icons to make them pop. Eco-Friendly Touch: Recyclable or biodegradable materials for the packaging. A small section emphasizing sustainability with a message like: “KRV is committed to beauty and the environment.” Unique Structural Design: Magnetic flap or window cutout to allow customers to peek at the product inside. A handle or carrying feature for easy transport, aligning with the portable nature of the dryer. Inspirational Touch: Include a short, empowering quote or message on the inside flap, such as: “Each look holds a moment—KRV lets you shape yours.” Custom Illustrations: Subtle, artistic illustrations (e.g., flowing hair, heat waves) integrated into the design background to emphasize beauty and technology. Additional Branding Elements: A tagline or hashtag like #KRVRadiance to encourage customers to share their experience on social media. Icons or badges for unique selling points, such as "Professional-Grade Quality" or "Salon Approved." Convenience Features: Printed assembly instructions or key features inside the box for ease of use. Perforated areas for easy opening. Color Gradients or Patterns: Add subtle gradients in the royal purple background for depth. Incorporate gold patterns (like geometric shapes or soft waves) for a modern touch. Seasonal or Limited-Edition Elements: A special ribbon or sticker indicating a “First Edition” or “Limited Release” to create exclusivity.
Should not have
• What the Packaging Should NOT Have Overcrowded Design: Avoid cluttering the box with too much text, small icons, or excessive design elements. A clean and elegant layout is key. Low-Quality Imagery: Do not use low-resolution product photos or stock images that don’t align with the premium look of your brand. Overused or Generic Icons: Skip overly common or generic symbols (e.g., basic checkmarks or lightning bolts). Custom, elegant icons are more appealing. Inconsistent Branding: Do not use colors, fonts, or design elements that stray from the royal purple, gold, and white branding. Consistency builds recognition. Unclear Information: Avoid vague or ambiguous descriptions. Clearly explain features, benefits, and product specifications. Cheap Materials: Packaging that feels flimsy or poorly constructed can reduce perceived value. Invest in durable materials. Overly Trendy Fonts: Avoid overly decorative or hard-to-read fonts. Stick with modern, clean typography that aligns with luxury branding. Busy Backgrounds: Don’t use loud patterns, excessive gradients, or background images that distract from key elements like the logo and product image. Misleading Claims: Avoid exaggerated or false claims (e.g., “World’s Best Dryer”) that could harm your brand’s credibility. Unnecessary Jargon: Avoid overly technical language that might confuse customers. Use simple, benefit-driven terms instead. Cliché Beauty Imagery: Skip generic, overused beauty symbols (e.g., oversized hair strands or glowing light effects) that don’t add value or originality. Lack of Contrast: Ensure text is easily readable. Avoid color combinations (like gold on light backgrounds) that reduce legibility. Lack of Accessibility: Don’t forget about inclusive design. Avoid small text or icons that are hard to read for visually impaired customers.

```html
<!DOCTYPE html>
<html lang="en">
<head>
<meta charset="utf-8">
<title>KRV Zenith Max Upright Dryer – Packaging Panels</title>
<link href="https://fonts.googleapis.com/css2?family=Cormorant+Garamond:ital,wght@0,400;0,500;0,600;1,400&family=Josefin+Sans:wght@400;600&display=swap" rel="stylesheet">
<style>
:root{
  --backdrop:#cfe2ea;
  --purple-deep:#2a1244;
  --purple:#4a2476;
  --purple-mid:#6b3a96;
  --orchid:#d892cf;
  --lavender:#a98bd0;
  --gold:#d9b65a;
  --gold-light:#f1dc92;
  --gold-dark:#a9822f;
  --silver:#dcd8e4;
  --hair:#8a6446;
  --hair-light:#c9a783;
  --white:#ffffff;
  --serif:'Cormorant Garamond', Georgia, serif;
  --sans:'Josefin Sans', Arial, sans-serif;
}
*{box-sizing:border-box;margin:0;padding:0}
html,body{width:1200px;height:1056px;overflow:hidden;background:var(--backdrop)}
.canvas{position:relative;width:1200px;height:1056px}
.panel{position:absolute;overflow:hidden;color:var(--white)}
.panel-frame{position:absolute;inset:12px;border:1.5px solid var(--gold);pointer-events:none}

/* top panel */
.top-panel{left:538px;top:70px;width:520px;height:396px;
  background:radial-gradient(ellipse at 50% 40%,var(--purple-mid) 0%,var(--purple) 45%,var(--purple-deep) 100%);}
.top-logo{position:absolute;left:0;right:0;top:120px;text-align:center;font-family:var(--serif);font-weight:500;font-size:120px;letter-spacing:6px;color:var(--silver);line-height:1}
.top-tagline{position:absolute;left:0;right:0;top:252px;text-align:center;font-family:var(--sans);font-size:13px;letter-spacing:6px;color:var(--silver)}

/* side panel */
.side-panel{left:142px;top:466px;width:396px;height:520px;
  background:linear-gradient(180deg,var(--purple) 0%,var(--purple-deep) 100%);}
.side-brand{position:absolute;left:0;right:0;top:40px;text-align:center;font-family:var(--serif);font-weight:600;font-size:44px;color:var(--gold);line-height:1}
.side-title{position:absolute;left:0;right:0;top:88px;text-align:center;font-family:var(--sans);font-size:19px;line-height:1.05;color:var(--white)}
.side-lead{position:absolute;left:0;right:0;top:136px;text-align:center;font-family:var(--serif);font-size:19px;color:var(--white)}
.side-heading{position:absolute;left:34px;font-family:var(--serif);font-size:15px;color:var(--white)}
.about-heading{top:166px}
.benefits-heading{top:234px}
.side-about{position:absolute;left:34px;right:34px;top:188px;font-family:var(--sans);font-size:9px;line-height:1.5;letter-spacing:.4px;text-transform:uppercase}
.benefit-row{position:absolute;left:34px;top:258px;display:flex;gap:18px}
.benefit{width:70px;text-align:center;font-family:var(--serif);font-size:10px;line-height:1.2}
.benefit small{display:block;font-size:8px;opacity:.85}
.gold-band{position:absolute;left:0;right:0;top:352px;height:46px;
  background:linear-gradient(90deg,var(--gold-dark),var(--gold-light) 40%,var(--gold) 70%,var(--gold-dark));}
.lifestyle-photo{position:absolute;right:30px;top:318px;width:112px;height:112px;border-radius:50%;border:3px solid var(--gold);
  background:linear-gradient(160deg,#efe6ea,#c9b3c2)}
.side-contact-title{position:absolute;left:34px;top:440px;font-family:var(--serif);font-size:18px}
.side-contact{position:absolute;left:34px;top:466px;font-family:var(--sans);font-size:9px;line-height:1.6;letter-spacing:.5px;text-transform:uppercase}

/* front panel */
.front-panel{left:538px;top:466px;width:520px;height:520px;
  background:
    radial-gradient(ellipse at 85% 20%,var(--orchid) 0%,rgba(216,146,207,0) 55%),
    linear-gradient(180deg,var(--purple-mid) 0%,var(--purple) 60%,var(--purple-deep) 100%);}
.front-logo{position:absolute;left:46px;top:44px;font-family:var(--serif);font-weight:500;font-size:64px;letter-spacing:2px;color:var(--silver);line-height:1}
.front-tagline{position:absolute;left:48px;top:116px;font-family:var(--sans);font-size:8px;letter-spacing:2.5px;color:var(--silver)}
.product-photo{position:absolute;left:240px;top:30px;width:230px;height:180px;border-radius:8px;
  background:linear-gradient(160deg,var(--lavender) 0%,var(--purple-mid) 100%);opacity:.85}
.hair-photo{position:absolute;left:330px;top:220px;width:176px;height:240px;border-radius:8px;
  background:linear-gradient(180deg,var(--hair) 0%,var(--hair-light) 100%)}
.front-brand{position:absolute;left:44px;top:192px;font-family:var(--serif);font-weight:600;font-size:80px;color:var(--gold);line-height:1}
.front-name{position:absolute;left:46px;top:282px;font-family:var(--sans);font-size:36px;line-height:1;color:var(--white)}
.front-type{position:absolute;left:48px;top:322px;font-family:var(--sans);font-weight:600;font-size:24px;line-height:1;color:var(--white)}
.gold-rule{position:absolute;left:48px;top:356px;width:246px;height:2px;background:var(--gold)}
.front-sub{position:absolute;left:48px;top:362px;font-family:var(--serif);font-style:italic;font-size:14px}
.feature-row{position:absolute;left:40px;top:390px;display:flex;gap:4px}
.feature{width:66px;text-align:center;font-family:var(--serif);font-size:8.5px;line-height:1.1;text-transform:uppercase}
.feature small{display:block;font-size:6px;margin-top:3px;opacity:.9}
.icon-disc{display:block;margin:0 auto 4px;width:36px;height:36px}
.front-cta{position:absolute;left:190px;width:300px;top:470px;text-align:center;font-family:var(--serif);font-size:12px;line-height:1.2;letter-spacing:.8px;text-transform:uppercase;color:var(--gold-light)}
</style>
</head>
<body>
<main class="canvas">

  <section class="panel top-panel" aria-label="Top panel">
    <div class="panel-frame"></div>
    <div class="top-logo">KRV</div>
    <div class="top-tagline">KIND, RADIANT, VIVID.</div>
  </section>

  <section class="panel side-panel" aria-label="Side panel">
    <div class="panel-frame"></div>
    <div class="side-brand">KRV</div>
    <div class="side-title">ZENITH MAX<br>UPRIGHT DRYER</div>
    <div class="side-lead">Experience professional styling at home.</div>
    <div class="side-heading about-heading">About The Product:</div>
    <p class="side-about">“At KRV, we believe beauty is power. Our tools are designed with precision, ensuring every style feels as beautiful as you are.”</p>
    <div class="side-heading benefits-heading">Key Benefits:</div>
    <div class="benefit-row">
      <div class="benefit">
        <svg class="icon-disc" viewBox="0 0 36 36"><circle cx="18" cy="18" r="16" fill="var(--gold)"/><path d="M11 11 L18 25 L25 11" fill="none" stroke="var(--purple-deep)" stroke-width="2.5"/></svg>
        Foldable Design<small>For Storage &amp; Travel</small>
      </div>
      <div class="benefit">
        <svg class="icon-disc" viewBox="0 0 36 36"><circle cx="18" cy="18" r="16" fill="var(--gold)"/><path d="M21 10 A9 9 0 1 0 26 22 A7 7 0 0 1 21 10 Z" fill="var(--purple-deep)"/></svg>
        Quiet Operation<small>For Comfortable Heat Control</small>
      </div>
      <div class="benefit">
        <svg class="icon-disc" viewBox="0 0 36 36"><circle cx="18" cy="18" r="16" fill="var(--gold)"/><rect x="16" y="8" width="4" height="14" rx="2" fill="var(--purple-deep)"/><circle cx="18" cy="24" r="4" fill="var(--purple-deep)"/></svg>
        3 Heat Settings<small>For Customizable Heat Control</small>
      </div>
    </div>
    <div class="gold-band"></div>
    <div class="lifestyle-photo" role="img" aria-label="Lifestyle photo of a woman using the upright dryer"></div>
    <div class="side-contact-title">Contact Informations:</div>
    <div class="side-contact">KRV Beauty | www.KRVhome.com<br>Customer Care: care@KRVhome.com</div>
  </section>

  <section class="panel front-panel" aria-label="Front panel">
    <div class="panel-frame"></div>
    <div class="front-logo">KRV</div>
    <div class="front-tagline">KIND, RADIANT, VIVID.</div>
    <div class="product-photo" role="img" aria-label="Product photo of the upright hood dryer"></div>
    <div class="hair-photo" role="img" aria-label="Photo of sleek, glossy brown hair"></div>
    <div class="front-brand">KRV</div>
    <div class="front-name">ZENITH MAX</div>
    <div class="front-type">UPRIGHT DRYER</div>
    <div class="gold-rule"></div>
    <div class="front-sub">Effortless Styling. Professional Results.</div>
    <div class="feature-row">
      <div class="feature">
        <svg class="icon-disc" viewBox="0 0 36 36"><circle cx="18" cy="18" r="16" fill="var(--gold)"/><path d="M18 9 V27 M14 13 L18 9 L22 13 M14 23 L18 27 L22 23" fill="none" stroke="var(--purple-deep)" stroke-width="2"/></svg>
        Adjustable Height<small>Perfect for all users and settings</small>
      </div>
      <div class="feature">
        <svg class="icon-disc" viewBox="0 0 36 36"><circle cx="18" cy="18" r="16" fill="var(--gold)"/><circle cx="18" cy="18" r="3" fill="var(--purple-deep)"/><g fill="var(--purple-deep)"><circle cx="11" cy="11" r="2"/><circle cx="25" cy="11" r="2"/><circle cx="11" cy="25" r="2"/><circle cx="25" cy="25" r="2"/></g><path d="M11 11 L25 25 M25 11 L11 25" stroke="var(--purple-deep)" stroke-width="1.5"/></svg>
        Ionic Technology<small>Faster drying, frizz-free result</small>
      </div>
      <div class="feature">
        <svg class="icon-disc" viewBox="0 0 36 36"><circle cx="18" cy="18" r="16" fill="var(--gold)"/><ellipse cx="18" cy="18" rx="10" ry="5" fill="none" stroke="var(--purple-deep)" stroke-width="1.8"/><path d="M18 9 V27" stroke="var(--purple-deep)" stroke-width="1.8"/></svg>
        360° Heat Technology<small>Even styling every time</small>
      </div>
      <div class="feature">
        <svg class="icon-disc" viewBox="0 0 36 36"><circle cx="18" cy="18" r="16" fill="var(--gold)"/><path d="M9 22 H20 L26 18 M9 26 H22 L28 21" fill="none" stroke="var(--purple-deep)" stroke-width="2"/><circle cx="19" cy="13" r="3" fill="var(--purple-deep)"/></svg>
        Lightweight and Portable<small>Easily movable and assemblable</small>
      </div>
    </div>
    <div class="front-cta">Elevate Your Look<br>with KRV Professional-Grade Tools</div>
  </section>

</main>
</body>
</html>
```